Redesign and move to Wordpress for corvandel.com

Our website needs a redesign and at the same time we are moving it to Wordpress. Please help us with a new digital professional look and feel.

We are an Australian Software Engineering company specialising in advanced software development using in A.I., PLatform Engineering, Integration and Cloud. See the current corvandel.com for more information about us.

```html
<!DOCTYPE html>
<html lang="en">
<head>
<meta charset="utf-8">
<title>Corvandel – Reliable Smart Software Engineering</title>
<link href="https://fonts.googleapis.com/css2?family=Audiowide&family=Roboto:ital,wght@0,400;0,500;0,700;1,400&display=swap" rel="stylesheet">
<style>
:root{
  --navy:#0f1e3d;
  --blue:#1b5aa8;
  --teal:#3fb8b4;
  --teal-dark:#2ea6a3;
  --ink:#1c1c1c;
  --muted:#6b6b6b;
  --line:#e6e6e6;
  --white:#ffffff;
  --footer:#0b0d10;
  --tag:#3d5a78;
}
*{box-sizing:border-box;margin:0;padding:0}
html,body{width:1200px;height:2714px;overflow:hidden}
body{font-family:"Roboto",sans-serif;color:var(--ink);background:var(--white);position:relative}
.abs{position:absolute}
.display{font-family:"Audiowide",sans-serif;font-weight:400;letter-spacing:.5px}

/* header + hero */
.hero{left:0;top:0;width:1200px;height:641px;overflow:hidden}
.hero-photo{position:absolute;inset:0;background:
  radial-gradient(ellipse 420px 380px at 880px 260px,rgba(190,150,120,.45),transparent 70%),
  radial-gradient(ellipse 500px 400px at 1050px 200px,rgba(40,140,150,.5),transparent 70%),
  linear-gradient(100deg,#16244a 0%,#1d3466 45%,#1f4a6e 75%,#183a52 100%)}
.brand{display:flex;align-items:center;gap:12px;color:var(--white);font-family:"Audiowide",sans-serif;font-size:24px;letter-spacing:1px}
.brand-mark{width:30px;height:30px;border:2px solid currentColor}
.hero .brand{left:131px;top:21px;height:34px}
.nav{left:366px;top:18px;width:424px;height:40px;border:1px solid rgba(255,255,255,.8);display:flex;align-items:center;padding:0 5px}
.nav a{color:var(--white);text-decoration:none;font-weight:700;font-size:14px;padding:6px 11px;margin-right:14px}
.nav a.active{background:var(--teal);padding:6px 10px}
.search{left:832px;top:18px;width:225px;height:40px;border:1px solid rgba(255,255,255,.8);display:flex;align-items:center;gap:8px;padding-left:16px;color:var(--white);font-size:11px}
.hero-title{left:130px;top:166px;color:var(--white);font-size:38px;line-height:64px;white-space:nowrap}
.hero-lead{left:131px;top:300px;color:var(--white);font-size:16px;font-weight:500;line-height:28px;white-space:nowrap}
.btn{background:var(--blue);color:var(--white);font-weight:700;font-size:15px;display:flex;align-items:center;justify-content:center;gap:8px;text-transform:uppercase}
.hero .btn{left:132px;top:396px;width:160px;height:48px}
.scroll{left:589px;top:566px}

/* partners */
.partner{top:688px;width:218px;height:71px;background:var(--white);box-shadow:0 2px 12px rgba(0,0,0,.07);display:flex;align-items:center;justify-content:center;font-weight:700;font-size:26px;color:#2a2a2a}
.rule{left:143px;top:812px;width:913px;height:1px;background:var(--line)}

/* services */
.section-title{width:1200px;left:0;text-align:center;font-size:33px;color:#111}
.services-title{top:862px}
.services-intro{left:100px;top:928px;width:1000px;text-align:center;font-size:13.5px;line-height:24px;color:#555;white-space:nowrap}
.card{top:1017px;width:218px;height:400px;background:var(--white);box-shadow:0 3px 14px rgba(0,0,0,.08);text-align:center}
.card-img{height:179px}
.card h3{font-weight:500;font-size:18px;margin-top:23px;color:#1a1a1a;white-space:nowrap}
.card .bar{width:40px;height:2px;background:var(--teal);margin:10px auto 0}
.card p{font-size:12.8px;line-height:21.5px;color:#666;margin-top:12px;height:65px;white-space:nowrap;letter-spacing:-.1px}
.card .btn{width:136px;height:40px;margin:21px auto 0;font-size:14px}
.circle-arrow{width:38px;height:38px;border-radius:50%;display:flex;align-items:center;justify-content:center}

/* newsletter */
.newsletter{left:0;top:1508px;width:1200px;height:365px;background:
  linear-gradient(180deg,var(--teal-dark) 0%,#49bdb8 50%,var(--teal-dark) 100%);text-align:center;color:var(--white)}
.newsletter h2{position:absolute;top:63px;width:100%;font-size:33px;line-height:56px}
.newsletter .sub{position:absolute;top:187px;width:100%;font-style:italic;font-size:18px}
.signup{left:379px;top:247px;width:442px;height:50px;background:var(--white);display:flex;align-items:center;padding:4px 5px 4px 17px;text-align:left}
.signup span{flex:1;font-size:11px;color:#aaa}
.signup .btn{width:136px;height:40px;font-size:14px}

/* news */
.news-title{top:1946px}
.post{top:2032px;width:288px;height:406px;background:var(--white);box-shadow:0 3px 14px rgba(0,0,0,.08);text-align:center}
.post-img{height:190px;position:relative}
.tag{position:absolute;left:35px;top:174px;width:217px;height:32px;background:var(--tag);color:var(--white);font-size:12px;display:flex;align-items:center;justify-content:center}
.post h3{font-weight:500;font-size:16px;line-height:25px;margin-top:34px;white-space:nowrap}
.post p{font-size:13.5px;line-height:22.5px;color:#666;margin-top:10px;white-space:nowrap}
.post .more{display:flex;justify-content:center;align-items:center;gap:6px;color:var(--blue);font-weight:700;font-size:14px;margin-top:13px}
.post-overlay-text{position:absolute;left:6px;right:6px;top:66px;color:var(--white);font-weight:700;font-size:20px;line-height:20px}

/* footer */
.footer{left:0;top:2512px;width:1200px;height:202px;background:var(--footer);color:var(--white)}
.footer .brand{position:absolute;left:138px;top:54px}
.copy{left:138px;top:122px;font-size:13px}
.footer h4{font-weight:500;font-size:15.5px;text-transform:uppercase}
.contact-row{display:flex;gap:10px;font-size:13px;line-height:24px;align-items:flex-start}
.ico{width:24px;height:24px;border-radius:50%;background:var(--white);display:flex;align-items:center;justify-content:center;flex:none}
.social{width:29px;height:29px;border-radius:50%;background:var(--white)}
</style>
</head>
<body>

<header class="abs hero">
  <div class="hero-photo" role="img" aria-label="Engineer in glasses looking at glowing code and data charts on screens"></div>
  <div class="abs brand"><span class="brand-mark"></span>corvandel</div>
  <nav class="abs nav">
    <a class="active">HOME</a><a>SERVICES</a><a>ABOUT</a><a>BLOG</a><a>CONTACT</a>
  </nav>
  <div class="abs search">
    <svg width="10" height="10" viewBox="0 0 10 10"><circle cx="4" cy="4" r="3" fill="none" stroke="#fff" stroke-width="1.6"/><line x1="6.2" y1="6.2" x2="9.3" y2="9.3" stroke="#fff" stroke-width="1.6"/></svg>
    Search
  </div>
  <h1 class="abs display hero-title">RELIABLE SMART<br>SOFTWARE ENGINEERING</h1>
  <p class="abs hero-lead">At Corvandel, we craft bespoke software solutions that are<br>&nbsp;not available on the market.</p>
  <div class="abs btn">GET STARTED
    <svg width="7" height="10" viewBox="0 0 7 10"><path d="M1 1l4 4-4 4" fill="none" stroke="#fff" stroke-width="1.6"/></svg></div>
  <svg class="abs scroll" width="22" height="54" viewBox="0 0 22 54"><rect x="2" y="1" width="17" height="29" rx="8.5" fill="none" stroke="#fff" stroke-width="1.6"/><line x1="10.5" y1="8" x2="10.5" y2="14" stroke="#fff" stroke-width="1.6"/><path d="M6 43l4.5 4.5L15 43" fill="none" stroke="#fff" stroke-width="1.6"/></svg>
</header>

<section aria-label="Clients">
  <div class="abs partner" style="left:140px">Halvero</div>
  <div class="abs partner" style="left:372px">Tranwick</div>
  <div class="abs partner" style="left:604px">Quorbyte</div>
  <div class="abs partner" style="left:836px">Brightfund</div>
  <div class="abs rule"></div>
</section>

<section aria-label="Our services">
  <h2 class="abs display section-title services-title">OUR SERVICES</h2>
  <p class="abs services-intro">At Corvandel, we craft bespoke software solutions that are not available on the market. By building organizations market-leading products, process automa-<br>tion, legacy system enablement, or advanced intelligent systems, we empower our customers to achieve a competitive edge in their industry.</p>

  <div class="abs circle-arrow" style="left:73px;top:1201px;background:#fff;box-shadow:0 2px 8px rgba(0,0,0,.15)">
    <svg width="8" height="12" viewBox="0 0 8 12"><path d="M6 1L1.5 6 6 11" fill="none" stroke="#222" stroke-width="1.8"/></svg></div>
  <div class="abs circle-arrow" style="left:1077px;top:1201px;background:var(--teal)">
    <svg width="8" height="12" viewBox="0 0 8 12"><path d="M2 1l4.5 5L2 11" fill="none" stroke="#fff" stroke-width="1.8"/></svg></div>

  <article class="abs card" style="left:132px">
    <div class="card-img" role="img" aria-label="Hands repairing circuit hardware" style="background:linear-gradient(135deg,#3a6fd0,#2a4d8f 60%,#545454)"></div>
    <h3>Microservices</h3><div class="bar"></div>
    <p>Leverage Microservices Architec-<br>ture to enable quick deployment,<br>dynamically scalable</p>
    <div class="btn">READ MORE <svg width="6" height="9" viewBox="0 0 6 9"><path d="M1 1l3.5 3.5L1 8" fill="none" stroke="#fff" stroke-width="1.5"/></svg></div>
  </article>
  <article class="abs card" style="left:367px">
    <div class="card-img" role="img" aria-label="Person typing on laptop with floating interface icons" style="background:linear-gradient(135deg,#7d9fe0,#3e5fb5 55%,#26356b)"></div>
    <h3>Platform Engineering</h3><div class="bar"></div>
    <p>For organisations looking to<br>manage the security and cost<br>risks around their cloud</p>
    <div class="btn">READ MORE <svg width="6" height="9" viewBox="0 0 6 9"><path d="M1 1l3.5 3.5L1 8" fill="none" stroke="#fff" stroke-width="1.5"/></svg></div>
  </article>
  <article class="abs card" style="left:601px;box-shadow:0 6px 20px rgba(0,0,0,.14)">
    <div class="card-img" role="img" aria-label="Hand holding a glowing chatbot hologram" style="background:linear-gradient(135deg,#0c1e4a,#1c3d86 50%,#4a5a7a)"></div>
    <h3>Conversational AI</h3><div class="bar"></div>
    <p>Enabling legacy systems with<br>conversational user interfaces, or<br>simply building intelligent</p>
    <div class="btn">READ MORE <svg width="6" height="9" viewBox="0 0 6 9"><path d="M1 1l3.5 3.5L1 8" fill="none" stroke="#fff" stroke-width="1.5"/></svg></div>
  </article>
  <article class="abs card" style="left:836px">
    <div class="card-img" role="img" aria-label="Business team working alongside a humanoid robot" style="background:linear-gradient(135deg,#1d2533,#3a4252 50%,#222a38)"></div>
    <h3>AI Agents</h3><div class="bar"></div>
    <p>The future of business AI are<br>autonomous agents that special-<br>ise in your business data</p>
    <div class="btn">READ MORE <svg width="6" height="9" viewBox="0 0 6 9"><path d="M1 1l3.5 3.5L1 8" fill="none" stroke="#fff" stroke-width="1.5"/></svg></div>
  </article>
</section>

<section class="abs newsletter" aria-label="Newsletter">
  <h2 class="display">AUSTRALIA'S LARGEST HEALTH CHARITY<br>IMPLEMENTS</h2>
  <p class="sub">Register To Our Newsletter To Find Out More</p>
  <div class="abs signup"><span>Enter Your Email</span>
    <div class="btn">SUBSCRIBE <svg width="6" height="9" viewBox="0 0 6 9"><path d="M1 1l3.5 3.5L1 8" fill="none" stroke="#fff" stroke-width="1.5"/></svg></div></div>
</section>

<section aria-label="Latest news">
  <h2 class="abs display section-title news-title">LATEST NEWS</h2>
  <svg class="abs" style="left:72px;top:2220px" width="22" height="34" viewBox="0 0 22 34"><path d="M18 2L4 17l14 15" fill="none" stroke="#9aa" stroke-width="3"/></svg>
  <svg class="abs" style="left:1106px;top:2220px" width="22" height="34" viewBox="0 0 22 34"><path d="M4 2l14 15L4 32" fill="none" stroke="var(--teal)" stroke-width="3"/></svg>

  <article class="abs post" style="left:144px">
    <div class="post-img" role="img" aria-label="Woman working on a laptop at a desk" style="background:linear-gradient(135deg,#d9d3c4,#b8a48a 50%,#8a7461)">
      <div class="tag">Net &amp; Nimbus</div></div>
    <h3>Lumo-4x: Lumera's New Flagship<br>Multimodeal Model Now ...</h3>
    <p>This groundbreaking multimodal model<br>integrates text, vision, and audio capabili-<br>ties, setting a new standard</p>
    <div class="more">READ MORE <svg width="6" height="9" viewBox="0 0 6 9"><path d="M1 1l3.5 3.5L1 8" fill="none" stroke="var(--blue)" stroke-width="1.5"/></svg></div>
  </article>
  <article class="abs post" style="left:456px">
    <div class="post-img" role="img" aria-label="Illustration of a lightbulb surrounded by responsible AI icons" style="background:linear-gradient(135deg,#1e9ad6,#2bb8c9 55%,#5fd49a)">
      <div class="tag">Artificial intelligence</div></div>
    <h3>Advancing Transparency: Updates<br>On Responsible Ai Research</h3>
    <p>A surge of generative AI models in the past<br>year has fueled much discussion about the<br>impact of artificial intelligence</p>
    <div class="more">READ MORE <svg width="6" height="9" viewBox="0 0 6 9"><path d="M1 1l3.5 3.5L1 8" fill="none" stroke="var(--blue)" stroke-width="1.5"/></svg></div>
  </article>
  <article class="abs post" style="left:767px">
    <div class="post-img" style="background:#050505">
      <div class="post-overlay-text">Shipping code quickly and safely in our own distributed environment</div>
      <div class="tag">Software Development</div></div>
    <h3>How Codehaven's Developer Experience<br>Team Improved Innerloop ...</h3>
    <p>This groundbreaking multimodal model<br>integrates text, vision, and audio capabili-<br>ties, setting a new standard</p>
    <div class="more">READ MORE <svg width="6" height="9" viewBox="0 0 6 9"><path d="M1 1l3.5 3.5L1 8" fill="none" stroke="var(--blue)" stroke-width="1.5"/></svg></div>
  </article>
</section>

<footer class="abs footer">
  <div class="brand"><span class="brand-mark"></span>corvandel</div>
  <p class="abs copy">© 2025 - Corvandel</p>

  <h4 class="abs" style="left:524px;top:60px">Contact Details</h4>
  <div class="abs contact-row" style="left:524px;top:97px">
    <span class="ico"><svg width="12" height="12" viewBox="0 0 12 12"><path d="M2.5 1l2 2.2-1 1.4c.8 1.6 1.8 2.6 3.4 3.4l1.4-1 2.2 2-1.2 1.6C5.5 10.4 1.6 6.5 1 2.2z" fill="#111"/></svg></span>
    <span>1800 555 019</span></div>
  <div class="abs contact-row" style="left:524px;top:135px">
    <span class="ico"><svg width="12" height="10" viewBox="0 0 12 10"><rect x="0.5" y="0.5" width="11" height="9" rx="1" fill="#111"/><path d="M1 1.5l5 4 5-4" fill="none" stroke="#fff" stroke-width="1.1"/></svg></span>
    <span>Suite 210, 48 Harbour Lane<br>Melbourne, VIC , 3000</span></div>

  <h4 class="abs" style="left:949px;top:60px">Follow Us</h4>
  <div class="abs social" role="img" aria-label="Social profile" style="left:950px;top:99px"></div>
  <div class="abs social" role="img" aria-label="Social profile" style="left:987px;top:99px;background:var(--teal)"></div>
  <div class="abs social" role="img" aria-label="Social profile" style="left:1026px;top:99px"></div>
</footer>

</body>
</html>
```